KBT Business Cards

We require business cards for our business. We would like a matte black back to the card, with our logo centred in the middle. The front side of the card is open to design.

Target Market(s)

Clients looking for legal services (professional)

Industry/Entity Type

Legal

Contact Information for Business Card

Doran Kelbrath
Partner
Mobile: 0461 738 524
Email: doran@kbtlaw.co
Website: www.kbtlaw.co
Level 3, 118 Wendmore Street
Sydney NSW 2000

Font styles to use
Other font styles liked:
• Avenir

Colors
f04a50
ffffff
1b1b1b

Requirements
Must have
• Black back with logo included in the centre of the card.
• Our font is Avenir.

```html
<!DOCTYPE html>
<html lang="en">
<head>
<meta charset="utf-8">
<title>KBT Business Cards</title>
<link rel="stylesheet" href="https://fonts.googleapis.com/css2?family=Roboto:wght@400;500&display=swap">
<style>
  :root {
    --red: #d0234a;
    --red-dark: #9e1c36;
    --ink: #1b1b1b;
    --card-black: #231f20;
    --grey-text: #4a4a4a;
    --white: #ffffff;
    --canvas: #e4e4e4;
  }
  * { margin: 0; padding: 0; box-sizing: border-box; }
  html, body {
    width: 1125px; height: 1200px; overflow: hidden;
    background: var(--canvas);
    font-family: "Roboto", Arial, sans-serif;
  }
  .card {
    position: absolute; left: 171px; width: 826px; height: 470px;
    overflow: hidden;
  }
  .card-front { top: 106px; background: var(--white); }
  .card-back { top: 639px; background: var(--card-black); }

  .firm-mark {
    position: absolute; left: 610px; top: 72px;
    display: flex; align-items: center; gap: 18px;
  }
  .firm-square { width: 34px; height: 34px; background: var(--red); flex: none; }
  .firm-name {
    font-weight: 500; font-size: 31px; line-height: 33px;
    color: var(--ink); text-transform: uppercase;
  }

  .contact { position: absolute; left: 43px; top: 252px; }
  .person-name { font-weight: 500; font-size: 31px; color: var(--red); line-height: 36px; }
  .person-role { font-weight: 500; font-size: 20px; color: var(--ink); line-height: 24px; }
  .address { margin-top: 14px; font-size: 19.5px; line-height: 25px; color: var(--grey-text); }
  .phone-email { margin-top: 8px; font-size: 19.5px; line-height: 25px; color: var(--grey-text); }

  .web-band { position: absolute; left: 0; bottom: 0; width: 826px; height: 42px; }
  .web-front {
    position: absolute; left: 43px; bottom: 9px;
    font-size: 19px; letter-spacing: 8.5px; color: var(--white);
  }

  .back-mark {
    position: absolute; left: 0; right: 0; top: 180px;
    display: flex; justify-content: center; align-items: center; gap: 22px;
  }
  .back-square { width: 44px; height: 44px; background: var(--red); }
  .back-name { font-weight: 500; font-size: 44px; color: var(--white); letter-spacing: 2px; }
  .web-back {
    position: absolute; left: 0; right: 0; top: 388px; text-align: center;
    font-size: 19px; letter-spacing: 13px; color: var(--white);
  }
</style>
</head>
<body>
  <section class="card card-front">
    <div class="firm-mark">
      <span class="firm-square"></span>
      <div class="firm-name">Kelbrath<br>Bevan Thorne<br>Legal</div>
    </div>

    <div class="contact">
      <p class="person-name">Doran Kelbrath</p>
      <p class="person-role">Partner</p>
      <p class="address">Level 3, 118 Wendmore Street<br>Sydney NSW 2000</p>
      <p class="phone-email">0461 738 524 | doran@kbtlaw.co</p>
    </div>

    <svg class="web-band" viewBox="0 0 826 42" aria-hidden="true">
      <defs>
        <linearGradient id="bandRed" x1="0" x2="1" y1="0" y2="0">
          <stop offset="0" stop-color="#a51d3a"/>
          <stop offset="1" stop-color="#d0234a"/>
        </linearGradient>
      </defs>
      <polygon points="400,30 826,30 826,42 412,42" fill="#231f20"/>
      <polygon points="0,0 372,0 412,42 0,42" fill="url(#bandRed)"/>
    </svg>
    <p class="web-front">www.kbtlaw.co</p>
  </section>

  <section class="card card-back">
    <div class="back-mark">
      <span class="back-square"></span>
      <span class="back-name">KBT</span>
    </div>
    <p class="web-back">WWW.KBTLAW.CO</p>
  </section>
</body>
</html>
```